Redesign Craft Brewing Recipe Website

Originally built with Bootstrap just to get the site going, I am seeking a complete redesign of the sites home page and recipe page. I am an experienced web developer with no graphic background, initially just looking for psd mocks.

I prefer styles that are clean and modern, and would prefer anything that is fun, engaging, and has an organic feel to it. I currently have a cartoon rabbit as a logo, but it needs some modification/tweaking, so any help in that area would be great as well.

Current site:
http://velvetfinch.cloudpagehost.net/

Current launch page/logo:
http://www.velvetfinch.com/

I like the overall layout of the elements currently, but the design sucks.

The launch page is at the following URL

Reason: Still looking for a more modern design. Designs received so far are too similar to the original.

My site is content based and does not contain images or products. Your design should not consist of large images.

Reason: The website has very little images, so the designs need to be more text and content based. The header needs to be very small and should not contain an ad rotater.

Target Market(s)

Home brewers, Craft brewers, Microbreweries, Brewpubs

Requirements
Must have
• Web 2.0 Look and Feel, Fun, Hip, Focus on content
Should not have
• A large photo as a header

```html
<!DOCTYPE html>
<html lang="en">
<head>
<meta charset="utf-8">
<title>Velvetfinch – Recipes</title>
<link href="https://fonts.googleapis.com/css2?family=Asap+Condensed:wght@400;700&family=Arimo:wght@400;700&display=swap" rel="stylesheet">
<style>
:root{
  --blue-top:#3596d6;
  --blue-bottom:#1f6db3;
  --ink:#222;
  --muted:#777;
  --link:#1a64b0;
  --line:#dcdcdc;
  --panel-border:#d6d6d6;
  --tile:#e9e9e9;
  --tag:#2a2a2a;
  --srm-pale:#e7e31b;
  --srm-dark:#170d0b;
  --srm-amber:#c68e3a;
  --go:#f4c000;
  --footer:#222;
  --white:#fff;
}
*{box-sizing:border-box;margin:0;padding:0}
html,body{width:1200px;height:1155px;overflow:hidden;background:var(--white)}
body{position:relative;font-family:"Arimo",Arial,sans-serif;color:var(--ink)}
.heading{font-family:"Asap Condensed","Arial Narrow",sans-serif;font-weight:400;text-transform:uppercase;letter-spacing:.3px}

/* Compact header */
.site-header{position:absolute;left:0;top:0;width:1200px;height:150px;background:linear-gradient(180deg,var(--blue-top),var(--blue-bottom))}
.header-fade{position:absolute;left:0;top:150px;width:1200px;height:20px;background:linear-gradient(180deg,#e6e6e6,#fff)}
.brand{position:absolute;left:177px;top:14px;font-family:"Asap Condensed",sans-serif;font-weight:700;font-size:34px;color:var(--white);letter-spacing:.5px}
.main-nav{position:absolute;left:725px;top:17px;width:296px;height:34px;border-radius:3px;background:linear-gradient(180deg,#fdfdfd,#d9d9d9);border:1px solid #c5c5c5;display:flex;align-items:center;padding-left:13px;font-size:12.7px;color:#666}
.main-nav .nav-link{padding:0 12px 0 10px;border-right:1px solid #c8c8c8;line-height:20px}
.main-nav .nav-link:first-child{padding-left:7px}
.social-btns{display:flex;gap:4px;margin-left:10px;font-size:9px}
.social-btns span{border:1px solid #c3cad8;background:#eef1f6;color:#3b5a98;padding:2px 4px;border-radius:2px}
.social-btns .count{background:#fff;color:#333}
.intro{position:absolute;left:177px;top:68px;width:845px;color:var(--white);font-size:10.2px;line-height:17px;text-align:justify}
.intro p+p{margin-top:6px}

/* Sidebar */
.search{position:absolute;left:177px;top:180px;width:252px;height:40px;background:#e8e8e8;border:1px solid #d0d0d0;border-radius:3px}
.search-field{position:absolute;left:5px;top:5px;width:201px;height:28px;background:#fff;border:1px solid #bdbdbd;border-radius:3px;font-size:10.5px;color:#aaa;line-height:26px;padding-left:11px}
.search-go{position:absolute;left:212px;top:5px;width:34px;height:28px;border-radius:4px;background:linear-gradient(180deg,#ffd73a,var(--go));border:1px solid #d9a400;color:#c07c00;font-size:12px;text-align:center;line-height:26px}

.filters{position:absolute;left:177px;top:238px;width:252px;height:448px;border:1px solid var(--panel-border);border-radius:3px;background:#fff}
.filter-title{position:absolute;left:14px;font-size:15.5px;color:#333}
.filter-list{position:absolute;left:15px;list-style:none;font-size:10.5px}
.filter-list li{height:23.7px;display:flex;align-items:center;gap:12px}
.check{width:11px;height:11px;border:1px solid #9a9a9a;background:linear-gradient(180deg,#fff,#e3e3e3)}
.divider{position:absolute;left:7px;width:238px;height:3px;background:#dcdcdc}
.scrollbar{position:absolute;left:223px;top:173px;width:13px;height:167px;background:#f0f0f0;border-left:1px solid #e2e2e2}
.scroll-thumb{position:absolute;left:1px;top:17px;width:11px;height:13px;background:#fafafa;border:1px solid #b5b5b5}
.scroll-up,.scroll-down{position:absolute;left:3px;width:0;height:0;border-left:3px solid transparent;border-right:3px solid transparent}
.scroll-up{top:5px;border-bottom:3px solid #555}
.scroll-down{bottom:5px;border-top:3px solid #555}

/* Recipes */
.tab{position:absolute;top:180px;width:88px;height:42px;border:1px solid var(--panel-border);border-bottom:none;border-radius:3px 3px 0 0;font-size:16px;text-align:center;line-height:40px;color:#333}
.tab.recent{left:448px;background:#fff;height:43px;z-index:2}
.tab.popular{left:545px;background:linear-gradient(180deg,#f2f2f2,#dcdcdc)}
.recipe-panel{position:absolute;left:438px;top:222px;width:584px;height:650px;border:1px solid var(--panel-border);border-radius:0 3px 3px 3px;padding:27px 11px 10px 12px;display:flex;flex-direction:column;gap:12px}
.recipe-card{height:196px;border:1px solid var(--panel-border);border-radius:3px;padding:0 6px}
.recipe-title{height:35px;padding:12px 7px 0;font-size:13px;line-height:16px;border-bottom:1px solid var(--line);color:#333}
.recipe-desc{margin:8px 7px 0;font-size:10.3px;line-height:17px;text-align:justify;height:51px}
.recipe-meta{margin-top:5px;padding:0 7px 8px;font-size:10.3px;line-height:17px;color:var(--muted);border-bottom:1px solid var(--line)}
.recipe-meta a{color:var(--link);text-decoration:none}
.recipe-foot{height:71px;padding:10px 3px 10px 10px;display:flex;align-items:center;justify-content:space-between;gap:8px}
.tags{display:flex;gap:10px;flex-shrink:0}
.tag{height:30px;padding:0 11px;background:var(--tag);color:var(--white);font-size:10.5px;line-height:30px;border-radius:3px;white-space:nowrap;box-shadow:0 0 0 1px #000 inset,0 2px 0 #555}
.stats{display:flex;gap:2px;flex-shrink:0}
.stat{width:50px;height:51px;background:var(--tile);border-radius:2px;font-size:10.3px;text-align:center;display:flex;flex-direction:column;justify-content:center;line-height:17px;color:#333}
.stat.srm-pale{background:var(--srm-pale)}
.stat.srm-dark{background:var(--srm-dark);color:var(--white)}
.stat.srm-amber{background:var(--srm-amber)}

/* Footer */
.site-footer{position:absolute;left:0;top:1100px;width:1200px;height:55px;background:var(--footer);color:var(--white);font-size:10.5px}
.legal{position:absolute;left:184px;top:20px}
.legal span{margin:0 5px}
.follow{position:absolute;left:861px;top:16px;display:flex;gap:11px}
.follow span{width:22px;height:22px;border-radius:3px;display:block}
</style>
</head>
<body>

<header class="site-header">
  <div class="brand">VELVETFINCH</div>
  <nav class="main-nav">
    <span class="nav-link">RECIPES</span>
    <span class="nav-link">LOGIN</span>
    <div class="social-btns"><span>Like</span><span class="count">0</span><span>Send</span></div>
  </nav>
  <div class="intro">
    <p>Pellentesque tristique mattis dui quis ullamcorper. In hac habitasse platea dictumst. Phasellus accumsan semper dui sit amet tempor.</p>
    <p>Integer fermentum posuere magna vitae ultrices. Praesent non nisi sit amet purus fringilla fringilla. Etiam in ante a felis dictum porttitor. Phasellus ut lorem et erat lacinia volutpat ut a mi. Lorem ipsum dolor sit amet, consectetur adipiscing elit. Quisque mollis volutpat nunc sit amet aliquam. Morbi enim neque, accumsan non egestas scelerisque, feugiat quis diam. Aliquam et massa ligula.</p>
  </div>
</header>
<div class="header-fade"></div>

<div class="search">
  <div class="search-field">Stout</div>
  <div class="search-go">GO</div>
</div>

<aside class="filters">
  <h3 class="filter-title heading" style="top:14px">Brewing</h3>
  <ul class="filter-list" style="top:44px">
    <li><span class="check"></span>Extract</li>
    <li><span class="check"></span>Partial Mash</li>
    <li><span class="check"></span>All Grain</li>
  </ul>
  <div class="divider" style="top:121px"></div>
  <h3 class="filter-title heading" style="top:131px">Styles</h3>
  <ul class="filter-list" style="top:161px">
    <li><span class="check"></span>American Amber Ale</li>
    <li><span class="check"></span>American Barleywine</li>
    <li><span class="check"></span>American Brown Ale</li>
    <li><span class="check"></span>American IPA</li>
    <li><span class="check"></span>American Pale Ale</li>
    <li><span class="check"></span>American Stout</li>
    <li><span class="check"></span>American Wheat or Rye Beer</li>
    <li><span class="check"></span>Applewine</li>
  </ul>
  <div class="scrollbar"><span class="scroll-up"></span><span class="scroll-thumb"></span><span class="scroll-down"></span></div>
  <div class="divider" style="top:365px"></div>
  <h3 class="filter-title heading" style="top:377px">Match Maker</h3>
  <ul class="filter-list" style="top:408px">
    <li><span class="check"></span>Boil Size</li>
  </ul>
</aside>

<div class="tab recent heading">Recent</div>
<div class="tab popular heading">Popular</div>

<main class="recipe-panel">
  <article class="recipe-card">
    <h2 class="recipe-title heading">Oak Bastard Sweet Mead</h2>
    <p class="recipe-desc">Lorem ipsum dolor sit amet, consectetur adipisicing elit, sed do eiusmod tempor incididunt ut labore et dolore magna aliqua.Suspendisse lobortis ullamcorper augue eget suscipit. Curabitur egestas euismod venenatis. Nulla facilisi. Maecenas id nisi nulla, eu feugiat neque.</p>
    <p class="recipe-meta">created by <a href="#">Daniel Marsh</a></p>
    <div class="recipe-foot">
      <div class="tags"><span class="tag">EXTRACT</span><span class="tag">SWEET MEAD</span></div>
      <div class="stats">
        <div class="stat">2.24%<span>abv</span></div>
        <div class="stat">24<span>ibu</span></div>
        <div class="stat">1.006<span>fg</span></div>
        <div class="stat">1.022<span>og</span></div>
        <div class="stat srm-pale">4<span>srm</span></div>
      </div>
    </div>
  </article>

  <article class="recipe-card">
    <h2 class="recipe-title heading">Venom Belgian Specialty Ale</h2>
    <p class="recipe-desc">Quisque mollis volutpat nunc sit amet aliquam. Morbi enim neque, accumsan non egestas scelerisque, feugiat quis diam. Aliquam et massa ligula. Pellentesque et elit ut justo bibendum consectetur. Donec non nisl eget libero pellentesque tristique. Aliquam erat volutpat. Donec at velit a ipsum ornare ornare.</p>
    <p class="recipe-meta">created by <a href="#">Daniel Marsh</a></p>
    <div class="recipe-foot">
      <div class="tags"><span class="tag">PARTIALMASH</span><span class="tag">BELGIAN SPECIALTY ALE</span></div>
      <div class="stats">
        <div class="stat">2.24%<span>abv</span></div>
        <div class="stat">24<span>ibu</span></div>
        <div class="stat">1.006<span>fg</span></div>
        <div class="stat">1.022<span>og</span></div>
        <div class="stat srm-dark">4<span>srm</span></div>
      </div>
    </div>
  </article>

  <article class="recipe-card">
    <h2 class="recipe-title heading">Honeysucker Belgian Tripel</h2>
    <p class="recipe-desc">Ut id tortor magna, eu tempus arcu. Donec diam nibh, egestas quis aliquet at, hendrerit semper eros. Vestibulum congue, turpis nec consequat tincidunt, dolor risus condimentum dolor, a sodales sapien augue sed mauris. Suspendisse libero felis, accumsan non scelerisque at, egestas at dui.</p>
    <p class="recipe-meta">created by <a href="#">Daniel Marsh</a></p>
    <div class="recipe-foot">
      <div class="tags"><span class="tag">PARTIALMASH</span><span class="tag">BELGIAN TRIPEL</span></div>
      <div class="stats">
        <div class="stat">2.24%<span>abv</span></div>
        <div class="stat">24<span>ibu</span></div>
        <div class="stat">1.006<span>fg</span></div>
        <div class="stat">1.022<span>og</span></div>
        <div class="stat srm-amber">4<span>srm</span></div>
      </div>
    </div>
  </article>
</main>

<footer class="site-footer">
  <div class="legal">© 2013, Velvetfinch, Inc. All Rights Reserved<span>|</span>Terms of Service<span>|</span>Contact</div>
  <div class="follow" aria-label="Social links">
    <span style="background:#4a67a6"></span>
    <span style="background:#4fb6e3"></span>
    <span style="background:#2a7fb8"></span>
    <span style="background:#f28a1e"></span>
    <span style="background:#5a9a3c"></span>
  </div>
</footer>

</body>
</html>
```